New Innovative Counselling and psychotherapy Service needs Business Card design

Keep it simple and professional. On one side, just company name and logo (perhaps in all blue) and maybe a tag line.

On other side (all white) my name and Qualifications in centre

Industry/Entity Type

Health And Wellness

Contact Information for Business Card

Dara Whelby
Counsellor & Psychotherapist
BSc (Psychol.), BA, Dip. (Couns. & Psych.), PG.Cert (CBT), FGTrK, ONRE

I will also require Mobile no, Email and web site address of which I'll pass on to final designer.

Font styles to use
Sans Serif

Requirements
Must have
• My Logo Only and please use the colours in logo that is in it.
Should not have
• Any other images

```html
<!DOCTYPE html>
<html lang="en">
<head>
<meta charset="utf-8">
<title>Calmer Harbour – Business Card</title>
<link href="https://fonts.googleapis.com/css2?family=Roboto:wght@400;500;700&display=swap" rel="stylesheet">
<style>
  :root {
    --sky: #4fb5ea;
    --leaf: #86c54d;
    --teal: #3aa89a;
    --ink: #2b2b2b;
    --ink-soft: #3c3c3c;
    --paper: #ffffff;
    --backdrop: #e9eaec;
  }
  * { margin: 0; padding: 0; box-sizing: border-box; }
  html, body { width: 1200px; height: 726px; overflow: hidden; }
  body {
    background: var(--backdrop);
    font-family: "Roboto", Arial, sans-serif;
    position: relative;
  }
  .card {
    position: absolute;
    top: 208px;
    width: 540px;
    height: 310px;
    box-shadow: 0 6px 18px rgba(0,0,0,0.12);
    overflow: hidden;
  }
  /* Front side */
  .card--front { left: 40px; background: var(--sky); }
  .front-brand {
    position: absolute;
    left: 0; right: 0; top: 112px;
    display: flex; align-items: center; justify-content: center; gap: 16px;
  }
  .brand-dot {
    width: 58px; height: 58px; border-radius: 50%;
    background: var(--paper);
    flex: none;
  }
  .front-text { color: var(--paper); }
  .front-name {
    font-size: 38px; font-weight: 400; line-height: 1;
    letter-spacing: 0.5px;
  }
  .front-tagline {
    margin-top: 8px;
    font-size: 13px; letter-spacing: 6.4px;
  }
  /* Back side */
  .card--back { left: 620px; background: var(--paper); }
  .holder {
    position: absolute; left: 34px; top: 66px;
    color: var(--ink-soft);
  }
  .holder-name {
    color: var(--sky); font-weight: 700; font-size: 22px;
    margin-bottom: 6px;
  }
  .holder-role, .holder-quals { font-size: 12.5px; line-height: 1.35; }
  .contacts {
    position: absolute; left: 34px; top: 192px;
    list-style: none;
    font-size: 14px; color: var(--ink);
  }
  .contacts li {
    display: flex; align-items: center; gap: 12px;
    height: 21px;
  }
  .contacts svg { width: 13px; height: 13px; flex: none; }
  .back-brand {
    position: absolute; right: 34px; top: 70px;
    display: flex; flex-direction: column; align-items: center; gap: 12px;
  }
  .back-brand .brand-dot { width: 74px; height: 74px; background: var(--sky); }
  .back-name { color: var(--ink); font-size: 22px; font-weight: 400; }
  .edge-band {
    position: absolute; left: 0; right: 0; bottom: 0; height: 8px;
    display: flex;
  }
  .edge-band__sky { flex: 0 0 64%; background: var(--sky); }
  .edge-band__leaf { flex: 1; background: var(--leaf); }
</style>
</head>
<body>
  <section class="card card--front" aria-label="Card front">
    <div class="front-brand">
      <span class="brand-dot"></span>
      <div class="front-text">
        <div class="front-name">Calmer Harbour</div>
        <div class="front-tagline">A tag line goes here</div>
      </div>
    </div>
  </section>

  <section class="card card--back" aria-label="Card back">
    <div class="holder">
      <h1 class="holder-name">Dara Whelby</h1>
      <p class="holder-role">Counsellor &amp; Psychotherapist</p>
      <p class="holder-quals">BSc (Psychol.), BA, Dip. (Couns. &amp; Psych.),<br>PG.Cert (CBT), FGTrK, ONRE</p>
    </div>

    <ul class="contacts">
      <li>
        <svg viewBox="0 0 16 16" aria-hidden="true"><path fill="#3aa89a" d="M3.5 1.5l2.6 2.8-1.4 1.8c.9 1.9 2.3 3.3 4.2 4.2l1.8-1.4 2.8 2.6-1.6 2.5C6.4 13.6 2.4 9.6 1 3.1z"/></svg>
        0123 456 7891
      </li>
      <li>
        <svg viewBox="0 0 16 16" aria-hidden="true"><rect x="1" y="3" width="14" height="10" fill="#3aa89a"/><path d="M1.5 3.5L8 9l6.5-5.5" stroke="#fff" stroke-width="1.3" fill="none"/></svg>
        dara.w@CalmerHarbour.com
      </li>
      <li>
        <svg viewBox="0 0 16 16" aria-hidden="true"><circle cx="8" cy="8" r="7" fill="#86c54d"/><path d="M1 8h14M8 1c-3 3.5-3 10.5 0 14M8 1c3 3.5 3 10.5 0 14" stroke="#fff" stroke-width="1" fill="none"/></svg>
        www.CalmerHarbour.com
      </li>
    </ul>

    <div class="back-brand">
      <span class="brand-dot"></span>
      <div class="back-name">Calmer Harbour</div>
    </div>

    <div class="edge-band"><span class="edge-band__sky"></span><span class="edge-band__leaf"></span></div>
  </section>
</body>
</html>
```